Professional Website for Leading Global Private Equity Real Estate Company

The company is a leading global Private Equity Real Estate (PERE). We need a homepage design, an inner page design, and color/font tweaks to the logo (color should be more soothing than current blue used in the logo). The logo website should project the company as global, professional, experienced, trustworthy, accessible, YOUNG, DYNAMIC, hi-tech. PLEASE SEE the attached Design Brief Word Doc for details.

Target Market(s)

institional investors and wealthy private individuals

Industry/Entity Type

Finance

Number of Pages Required

2 page

Font styles to use
Sans Serif
Other font styles liked:
• either like in https://www.ferndalequay.com/ or like in presentations (Montserrat Black & Montserrat Light, Century Gothic, Blair ITC, Almoni Neue DL 4.0 AAA Medium, Almoni DL AAA)

Requirements
Must have
• new color palette that is NOT based on current logo. they want a more soothing color palette than the blue in that logo. the new color palette should project: global, professional, experienced, trustworthy, accessible, YOUNG, DYNAMIC, hi-tech.
Nice to have
• the likes these sites: https://www.ferndalequay.com/ and https://www.tvr.law/

```html
<!DOCTYPE html>
<html lang="en">
<head>
<meta charset="utf-8">
<title>Veltara Real Estate — Leading Global Private Equity Real Estate</title>
<link rel="stylesheet" href="https://fonts.googleapis.com/css2?family=Syncopate:wght@400;700&family=Inter:wght@400;500;600&display=swap">
<style>
:root{
  --navy-900:#111c24;
  --navy-800:#16242e;
  --navy-700:#1c2e3a;
  --navy-600:#24394a;
  --slate-500:#3b5264;
  --green:#2fa66b;
  --green-light:#3cb879;
  --white:#ffffff;
  --muted:#c9d3db;
  --line:#5d7383;
  --display:'Syncopate',sans-serif;
  --body:'Inter',sans-serif;
}
*{box-sizing:border-box;margin:0;padding:0}
html,body{width:1200px;height:4454px;overflow:hidden}
body{position:relative;background:var(--navy-800);color:var(--white);font-family:var(--body)}
.abs{position:absolute}
.display{font-family:var(--display);text-transform:uppercase;letter-spacing:.04em}

/* header + hero */
.hero{left:0;top:0;width:1200px;height:697px;
  background:linear-gradient(180deg,#1b3a8c 0%,#3c4f9b 22%,#8a6c8f 36%,#3a4556 52%,#26323d 75%,#1d2a33 100%)}
.hero-photo{left:0;top:0;width:1200px;height:697px}
.brand{left:98px;top:22px;display:flex;align-items:center;gap:12px}
.brand-dot{width:52px;height:52px;border-radius:50%;background:var(--white)}
.brand-name{font-family:var(--body);font-weight:500;font-size:20px;line-height:24px;letter-spacing:.06em;color:var(--white)}
.nav{left:414px;top:38px;display:flex;gap:40px;font-size:12px;font-weight:500;letter-spacing:.02em}
.nav span{white-space:nowrap}
.login{left:1008px;top:29px;width:104px;height:34px;border:1.5px solid var(--white);font-size:12px;display:flex;align-items:center;justify-content:center}
.hero-kicker{left:104px;top:242px;font-size:16px;letter-spacing:.22em}
.hero-title{left:100px;top:272px;font-size:40px;line-height:41px;font-weight:700;letter-spacing:.02em}
.btn-outline{border:1.5px solid var(--white);display:flex;align-items:center;justify-content:center;font-size:13px;letter-spacing:.1em;font-family:var(--display)}
.hero-btn{left:110px;top:414px;width:156px;height:39px}
.play{left:768px;top:264px}
.scroll{left:0;width:1200px;top:622px;text-align:center;font-size:11px;letter-spacing:.18em;font-family:var(--display)}

/* sections */
.band-about{left:0;top:697px;width:1200px;height:1380px;background:linear-gradient(180deg,#17252f 0%,#1b2c38 40%,#263b4a 55%,#1d2f3b 75%,#17252f 100%)}
.band-edge{left:0;top:2077px;width:1200px;height:910px;background:linear-gradient(180deg,#17252f 0%,#1c2d39 45%,#2a4152 75%,#213545 100%)}
.band-resp{left:0;top:2987px;width:1200px;height:1150px;background:linear-gradient(180deg,#213545 0%,#1e3241 40%,#2b4151 65%,#22384a 100%)}
.footer{left:0;top:4137px;width:1200px;height:317px;background:var(--navy-800)}

.eyebrow{font-family:var(--display);font-size:12px;letter-spacing:.2em;text-align:center;width:1200px;left:0}
.section-title{font-family:var(--display);font-size:32px;letter-spacing:.04em;text-align:center;width:1200px;left:0;line-height:36px}
.title-rule{left:570px;top:885px;width:58px;height:2px;background:var(--slate-500)}
.about-copy{left:170px;top:914px;width:860px;text-align:center;font-size:18.5px;line-height:31px;color:var(--muted)}
.stats{left:0;top:1070px;width:1200px}
.stat{position:absolute;top:0}
.stat b{display:block;font-family:var(--display);font-weight:400;font-size:34px;line-height:40px}
.stat span{display:block;font-size:15px;margin-top:6px;color:var(--muted)}
.vrule{width:1.5px;background:var(--line)}

.card{width:315px;height:218px;overflow:hidden}
.card-photo{width:100%;height:100%}
.card-label{position:absolute;left:0;width:100%;bottom:14px;text-align:center;font-family:var(--display);font-weight:700;font-size:15px;letter-spacing:.04em}
.card-active{background:var(--green)}
.card-active .frame{position:absolute;left:8px;top:8px;right:8px;bottom:8px;border:1.5px solid rgba(255,255,255,.7)}
.card-active .inner{position:absolute;left:0;top:58px;width:100%;text-align:center}
.card-active .k{font-family:var(--display);font-size:13px;letter-spacing:.05em}
.card-active .t{font-family:var(--display);font-weight:700;font-size:15px;letter-spacing:.04em;margin-top:2px}
.card-active p{font-size:11.5px;line-height:15px;color:#d9f1e4;margin:8px auto 0;width:250px}
.card-active .more{margin:12px auto 0;width:128px;height:30px;border:1.5px solid var(--white);font-family:var(--display);font-size:9.5px;letter-spacing:.08em;display:flex;align-items:center;justify-content:center}

.edge-circle{left:150px;top:2117px;width:418px;height:418px;border-radius:50%;background:linear-gradient(135deg,#e8eef4 0%,#a9bccd 40%,#55738c 70%,#2c4358 100%)}
.split-title{font-family:var(--display);font-size:30px;letter-spacing:.04em}
.split-copy{font-size:15.5px;line-height:27px;color:var(--muted)}
.split-copy p+p{margin-top:12px}
.btn-solid{background:var(--green);display:flex;align-items:center;justify-content:center;font-family:var(--display);font-weight:700;font-size:12.5px;letter-spacing:.08em}
.btn-line{border:2px solid var(--green);display:flex;align-items:center;justify-content:center;font-family:var(--display);font-weight:700;font-size:12.5px;letter-spacing:.08em}

.stay-sub{left:0;width:1200px;text-align:center;top:2770px;font-size:16.5px;color:var(--muted)}
.field{border:1.5px solid var(--line);height:48px;font-size:12px;padding:0 18px;display:flex;align-items:center;color:var(--muted);letter-spacing:.03em}

.resp-photo{left:602px;top:3078px;width:598px;height:453px;background:linear-gradient(135deg,#8c9aa5 0%,#c8ccce 35%,#e7e6e1 55%,#9aa5ac 80%,#5c6b77 100%)}
.resp-rule{left:121px;top:3177px;width:58px;height:3px;background:var(--white)}

.contact-eyebrow{left:130px;top:3690px;font-family:var(--display);font-size:12px;letter-spacing:.18em}
.contact-title{left:128px;top:3712px;font-family:var(--display);font-size:30px;line-height:35px;letter-spacing:.03em}
.contact-line{display:flex;align-items:center;gap:12px;font-size:17px}
.ico{width:26px;height:26px;border-radius:50%;background:var(--white);display:flex;align-items:center;justify-content:center}
.form-field{border-bottom:1.5px solid var(--line);height:30px;display:flex;align-items:center;gap:8px;font-size:13px;color:var(--muted);padding-left:6px}

.foot-head{font-family:var(--display);font-size:12.5px;letter-spacing:.06em;font-weight:700}
.foot-list{list-style:none;font-size:12.5px;line-height:27px;color:var(--muted)}
.foot-rule{width:1.5px;background:var(--slate-500)}
.foot-contact{display:flex;gap:14px;font-size:12.5px;color:var(--muted);line-height:15px}
.foot-bottom{left:0;top:4386px;width:1200px;height:1px;background:var(--slate-500)}
.legal{font-size:11.5px;color:var(--muted)}
.socials{display:flex;gap:6px}
.socials i{width:26px;height:26px;border-radius:50%;background:var(--white);display:block}
</style>
</head>
<body>

<!-- Hero -->
<section class="abs hero">
  <div class="abs hero-photo" role="img" aria-label="Snow-capped mountain range under a blue and violet dusk sky"></div>
</section>
<header>
  <div class="abs brand"><span class="brand-dot"></span><span class="brand-name">VELTARA<br>REAL ESTATE</span></div>
  <nav class="abs nav">
    <span>ABOUT US ⌄</span><span>OUR BUSINESSES ⌄</span><span>INVESTORS LOBBY</span><span style="margin-left:6px">NEWS</span><span>CONTACT US</span>
  </nav>
  <div class="abs login">LOG IN</div>
</header>
<div class="abs hero-kicker display">Veltara Real Estate</div>
<h1 class="abs hero-title display">Leading Global<br>Private Equity<br>Real Estate</h1>
<div class="abs btn-outline hero-btn">ABOUT US</div>
<svg class="abs play" width="104" height="104" viewBox="0 0 104 104" aria-label="Play video">
  <circle cx="52" cy="52" r="50" fill="none" stroke="#fff" stroke-width="1.5"/>
  <circle cx="52" cy="52" r="42" fill="#fff"/>
  <path d="M44 34 L70 52 L44 70 Z" fill="#111c24"/>
</svg>
<div class="abs scroll">SCROLL DOWN
  <svg width="20" height="14" viewBox="0 0 20 14" style="display:block;margin:8px auto 0"><path d="M3 3 L10 10 L17 3" fill="none" stroke="#fff" stroke-width="3"/></svg>
</div>

<!-- Who we are -->
<section class="abs band-about" role="img" aria-label="Faint dark mountain landscape backdrop"></section>
<div class="abs eyebrow" style="top:822px">WHO WE ARE</div>
<h2 class="abs section-title" style="top:842px">Veltara Real Estate</h2>
<div class="abs title-rule"></div>
<p class="abs about-copy">Lorem ipsum dolor sit amet, consectetur adipiscing elit, sed do eiusmod tempor incidi-dunt ut labore et doloreUt enim ad minim veniam, quis nostrud exercitation ullamcoea Lorem ipsum dolor sit amet, consectetur adipiscingLorem ipsum dolor sit.</p>
<div class="abs stats">
  <div class="stat" style="left:138px"><b>$250</b><span>REAL ESTATE PROJECTS</span></div>
  <div class="abs vrule" style="left:368px;top:6px;height:56px"></div>
  <div class="stat" style="left:415px"><b>$25B</b><span>PRIVATE EQUITY</span></div>
  <div class="abs vrule" style="left:607px;top:6px;height:56px"></div>
  <div class="stat" style="left:656px"><b>$13B</b><span>FUND SOLUTIONS</span></div>
  <div class="abs vrule" style="left:845px;top:6px;height:56px"></div>
  <div class="stat" style="left:905px"><b>$120B</b><span>CREDIT &amp; INSURANCE</span></div>
</div>
<div class="abs vrule" style="left:606px;top:1259px;height:55px;background:var(--muted)"></div>

<!-- Platforms -->
<div class="abs eyebrow" style="top:1374px">SERVICES PLATFORM</div>
<h2 class="abs section-title" style="top:1396px">Our Investment<br>Platforms</h2>

<div class="abs card" style="left:118px;top:1508px">
  <div class="card-photo" role="img" aria-label="Glass office tower seen from below against a blue sky" style="background:linear-gradient(135deg,#d9e2ea 0%,#7f9ab3 40%,#2f4f72 75%,#1d3047 100%)"></div>
  <div class="card-label">Lorem Ipsum Dolor Sit</div>
</div>
<div class="abs card card-active" style="left:444px;top:1508px">
  <div class="frame"></div>
  <div class="inner">
    <div class="k">SED PERSPICIATI</div>
    <div class="t">LOREM IPSUM DOLOR SIT</div>
    <p>Lorem ipsum dolor sit amet, consectetur adipiscing elit sed do eiusmod tempor</p>
    <div class="more">LEARN MORE</div>
  </div>
</div>
<div class="abs card" style="left:773px;top:1508px">
  <div class="card-photo" role="img" aria-label="Dark skyscrapers rising into a cloudy sky" style="background:linear-gradient(160deg,#e3e8ec 0%,#a5b2bd 35%,#3b4856 65%,#1b242d 100%)"></div>
  <div class="card-label">Lorem Ipsum Dolor Sit</div>
</div>
<div class="abs card" style="left:280px;top:1743px">
  <div class="card-photo" role="img" aria-label="Office building facade at night with pink lit windows" style="background:linear-gradient(135deg,#1b1a2a 0%,#5b2c4c 40%,#b4506e 60%,#2a2436 100%)"></div>
  <div class="card-label">Lorem Ipsum Dolor Sit</div>
</div>
<div class="abs card" style="left:607px;top:1743px">
  <div class="card-photo" role="img" aria-label="Glass tower rising into a blue sky with white clouds" style="background:linear-gradient(160deg,#eef3f7 0%,#a9c2d9 40%,#4a7398 75%,#2a4a6b 100%)"></div>
  <div class="card-label">Lorem Ipsum Dolor Sit</div>
</div>

<!-- Our edge -->
<section class="abs band-edge" role="img" aria-label="Dark mountain landscape backdrop"></section>
<div class="abs edge-circle" role="img" aria-label="Round crop of a glass building reflecting clouds"></div>
<h2 class="abs split-title" style="left:643px;top:2188px">Our Edge</h2>
<div class="abs split-copy" style="left:645px;top:2256px;width:450px">
  <p>Lorem ipsum dolor sit amet, consectetur adipiscing elit, sed do eiusmod tempor incididunt ut co laboris nisi ut aliquip ex ea commodo consequat.</p>
  <p>Aabor et dolore magna aliqua. Ut enim ad minim veniam, quis nostrud exercitation ullamco laboris &nbsp;et dolore</p>
</div>
<div class="abs btn-solid" style="left:645px;top:2434px;width:260px;height:49px">INVESTOR INFORMATION</div>

<!-- Stay updated -->
<h2 class="abs section-title" style="top:2716px">Stay Updated</h2>
<p class="abs stay-sub">Get our latest insights, firm announcements and Charitable Foundation updates.</p>
<div class="abs field" style="left:220px;top:2822px;width:293px">NAME*</div>
<div class="abs field" style="left:520px;top:2822px;width:294px">EMAIL*</div>
<div class="abs btn-solid" style="left:821px;top:2822px;width:190px;height:48px;font-size:14px">SUBSCRIBE</div>

<!-- Responsibility -->
<section class="abs band-resp" role="img" aria-label="Soft mountain landscape backdrop"></section>
<div class="abs resp-photo" role="img" aria-label="Team of colleagues working together around a laptop in a bright office"></div>
<h2 class="abs split-title" style="left:121px;top:3135px">Our Responsibility</h2>
<div class="abs resp-rule"></div>
<div class="abs split-copy" style="left:121px;top:3202px;width:450px">
  <p>Lorem ipsum dolor sit amet, consectetur adipiscing elit, sed do eiusmod tempor incididunt ut co laboris nisi ut aliquip ex ea commodo consequat.</p>
  <p>Aabor et dolore magna aliqua. Ut enim ad minim veniam, quis nostrud exercitation ullamco laboris &nbsp;et dolore</p>
</div>
<div class="abs btn-line" style="left:116px;top:3385px;width:261px;height:51px">INVESTOR INFORMATION</div>

<!-- Contact -->
<div class="abs contact-eyebrow">CONTACT US</div>
<h2 class="abs contact-title">Get In Touch<br>With Us</h2>
<div class="abs contact-line" style="left:130px;top:3808px">
  <span class="ico"><svg width="14" height="14" viewBox="0 0 24 24"><path d="M6.6 10.8a15 15 0 0 0 6.6 6.6l2.2-2.2a1 1 0 0 1 1-.25 11.4 11.4 0 0 0 3.6.57 1 1 0 0 1 1 1V20a1 1 0 0 1-1 1A17 17 0 0 1 3 4a1 1 0 0 1 1-1h3.5a1 1 0 0 1 1 1c0 1.25.2 2.45.57 3.57a1 1 0 0 1-.25 1z" fill="#16242e"/></svg></span>555-014-2290
</div>
<div class="abs contact-line" style="left:132px;top:3855px">
  <span class="ico"><svg width="14" height="12" viewBox="0 0 24 20"><rect x="1" y="2" width="22" height="16" rx="2" fill="none" stroke="#16242e" stroke-width="2.4"/><path d="M2 4 L12 11 L22 4" fill="none" stroke="#16242e" stroke-width="2.4"/></svg></span>hello@veltararealty.com
</div>

<div class="abs form-field" style="left:496px;top:3688px;width:260px">
  <svg width="14" height="14" viewBox="0 0 24 24"><circle cx="12" cy="8" r="4.5" fill="none" stroke="#c9d3db" stroke-width="2"/><path d="M3 22c1.5-5 4.8-7 9-7s7.5 2 9 7" fill="none" stroke="#c9d3db" stroke-width="2"/></svg>First Name</div>
<div class="abs form-field" style="left:783px;top:3688px;width:260px">
  <svg width="14" height="14" viewBox="0 0 24 24"><circle cx="12" cy="8" r="4.5" fill="none" stroke="#c9d3db" stroke-width="2"/><path d="M3 22c1.5-5 4.8-7 9-7s7.5 2 9 7" fill="none" stroke="#c9d3db" stroke-width="2"/></svg>Last Name</div>
<div class="abs form-field" style="left:496px;top:3748px;width:260px">
  <svg width="14" height="14" viewBox="0 0 24 24"><path d="M6.6 10.8a15 15 0 0 0 6.6 6.6l2.2-2.2a1 1 0 0 1 1-.25 11.4 11.4 0 0 0 3.6.57 1 1 0 0 1 1 1V20a1 1 0 0 1-1 1A17 17 0 0 1 3 4a1 1 0 0 1 1-1h3.5a1 1 0 0 1 1 1c0 1.25.2 2.45.57 3.57a1 1 0 0 1-.25 1z" fill="none" stroke="#c9d3db" stroke-width="1.8"/></svg>Phone Number</div>
<div class="abs form-field" style="left:783px;top:3748px;width:260px">
  <svg width="14" height="12" viewBox="0 0 24 20"><rect x="1" y="2" width="22" height="16" rx="2" fill="none" stroke="#c9d3db" stroke-width="2"/><path d="M2 4 L12 11 L22 4" fill="none" stroke="#c9d3db" stroke-width="2"/></svg>Email address</div>
<div class="abs form-field" style="left:496px;top:3800px;width:547px;height:90px;align-items:flex-start;padding-top:6px">Message</div>
<div class="abs btn-solid" style="left:500px;top:3916px;width:190px;height:45px;font-family:var(--body);font-weight:600;font-size:14px;letter-spacing:.02em">SUBMIT MESSAGE</div>

<!-- Footer -->
<footer class="abs footer"></footer>
<div class="abs foot-head" style="left:133px;top:4148px">IMPORTANT LINKS</div>
<ul class="abs foot-list" style="left:133px;top:4176px">
  <li>About Us</li><li>Our Businesses</li><li>Investor Lobby</li><li>News</li><li>Contact Us</li>
</ul>
<div class="abs foot-rule" style="left:329px;top:4146px;height:197px"></div>
<div class="abs foot-head" style="left:380px;top:4148px">EXPLORE VELTARA REAL ESTATE</div>
<ul class="abs foot-list" style="left:382px;top:4182px">
  <li>Private Equity</li><li>Real Estate</li><li>Credit</li><li>Strategic Partners</li><li>Tactical Opportunities</li><li>Infrastructure</li>
</ul>
<ul class="abs foot-list" style="left:585px;top:4182px">
  <li>Insurance Solutions</li><li>Life Sciences</li><li>Portfolio Operations</li><li>Technology and Innovations</li><li>Registered Products</li>
</ul>
<div class="abs foot-rule" style="left:806px;top:4146px;height:197px"></div>
<div class="abs foot-head" style="left:856px;top:4148px">CONTACT DETAILS</div>
<div class="abs foot-contact" style="left:856px;top:4183px">
  <span class="ico"><svg width="12" height="14" viewBox="0 0 24 28"><path d="M12 1a9 9 0 0 0-9 9c0 7 9 17 9 17s9-10 9-17a9 9 0 0 0-9-9z" fill="#16242e"/><circle cx="12" cy="10" r="3.5" fill="#fff"/></svg></span>
  <span>48 Harbor Row Suite 2<br>Bayview, FL 30000</span>
</div>
<div class="abs foot-contact" style="left:856px;top:4232px;align-items:center">
  <span class="ico"><svg width="13" height="13" viewBox="0 0 24 24"><path d="M6.6 10.8a15 15 0 0 0 6.6 6.6l2.2-2.2a1 1 0 0 1 1-.25 11.4 11.4 0 0 0 3.6.57 1 1 0 0 1 1 1V20a1 1 0 0 1-1 1A17 17 0 0 1 3 4a1 1 0 0 1 1-1h3.5a1 1 0 0 1 1 1c0 1.25.2 2.45.57 3.57a1 1 0 0 1-.25 1z" fill="#16242e"/></svg></span>555-014-2290
</div>
<div class="abs foot-contact" style="left:856px;top:4268px;align-items:center">
  <span class="ico"><svg width="13" height="11" viewBox="0 0 24 20"><rect x="1" y="2" width="22" height="16" rx="2" fill="none" stroke="#16242e" stroke-width="2.4"/><path d="M2 4 L12 11 L22 4" fill="none" stroke="#16242e" stroke-width="2.4"/></svg></span>hello@veltararealty.com
</div>
<div class="abs socials" style="left:858px;top:4310px" aria-label="Social media links"><i></i><i></i><i></i><i></i></div>
<div class="abs foot-bottom"></div>
<div class="abs legal" style="left:126px;top:4412px">Copyright © 2022 Veltara Realestate</div>
<div class="abs legal" style="left:842px;top:4412px">Terms of Use &nbsp;| &nbsp;Sitemap &nbsp;| &nbsp;Privacy Policy</div>

</body>
</html>
```